Harbourline Electrical Solutions

On one side. LOGO (underneath:) Commercial Industrial Residential

- NAME & CONTACT DETAILS

Marcus T. Hollings
Project Manager

(Cell icon) (441) 555-0187
(Email icon) hlelectricalsolutions@mailvento.com
(plain circle & plain circle icons )@hlelectricalsolutions

Other side: LOGO - underneath ELECTRICAL CONSTRUCTION & MAINTENANCE . LED LIGHTING & AUTOMATION . LIFE SAFETY SYSTEMS (FIRE ALARM / SECURITY) . DATA & COMMUNICATION

```html
<!DOCTYPE html>
<html lang="en">
<head>
<meta charset="utf-8">
<title>Harbourline Electrical Solutions – Business Cards</title>
<link href="https://fonts.googleapis.com/css2?family=Montserrat:wght@700&family=Lato:wght@300;400&family=Roboto+Condensed:wght@400&display=swap" rel="stylesheet">
<style>
  :root {
    --backdrop: #0b0b0d;
    --card: #2a2a2c;
    --card-edge: #1c6076;
    --ink: #f2f2f2;
    --ink-soft: #cfcfcf;
    --ink-muted: #8d8d90;
    --rule: #6a6a6d;
  }
  * { margin: 0; padding: 0; box-sizing: border-box; }
  html, body {
    width: 1200px; height: 822px; overflow: hidden;
    background: var(--backdrop);
  }
  .canvas {
    width: 1200px; height: 822px;
    display: flex; align-items: center; justify-content: center; gap: 56px;
  }
  .card {
    width: 532px; height: 304px;
    background: var(--card);
    border-bottom: 3px solid var(--card-edge);
    border-right: 3px solid var(--card-edge);
    border-radius: 2px;
    display: flex; flex-direction: column; align-items: center; justify-content: center;
    color: var(--ink);
  }

  /* Contact side */
  .contact-name {
    font-family: "Montserrat", sans-serif; font-weight: 700;
    font-size: 17px; letter-spacing: 0.5px; text-transform: uppercase;
  }
  .contact-role {
    font-family: "Lato", sans-serif; font-weight: 300;
    font-size: 14px; color: var(--ink-soft); margin-top: 1px;
  }
  .icon-row {
    display: flex; align-items: center; gap: 5px; margin: 7px 0 5px;
  }
  .icon-row .rule { width: 44px; height: 1px; background: var(--rule); }
  .icon-row .rule:first-child { margin-right: 5px; }
  .icon-row .rule:last-child { margin-left: 5px; }
  .icon-badge {
    width: 22px; height: 22px; border: 1.3px solid var(--ink);
    border-radius: 50%; display: flex; align-items: center; justify-content: center;
  }
  .icon-badge svg { width: 12px; height: 12px; }
  .contact-line {
    font-family: "Lato", sans-serif; font-weight: 400;
    font-size: 14px; color: var(--ink-soft); line-height: 1.35;
  }
  .contact-block { text-align: center; }

  /* Brand side */
  .brand-side { align-items: center; }
  .brand-lockup {
    display: flex; align-items: center; gap: 10px;
  }
  .brand-square { width: 14px; height: 14px; background: var(--ink-muted); }
  .brand-name {
    font-family: "Roboto Condensed", sans-serif; font-weight: 400;
    font-size: 24px; letter-spacing: 2px; text-transform: uppercase;
    color: var(--ink-muted);
  }
  .brand-sectors {
    font-family: "Roboto Condensed", sans-serif; font-size: 12px;
    letter-spacing: 0.6px; color: var(--ink-muted); margin-top: 8px;
    text-transform: uppercase;
  }
  .brand-divider { width: 300px; height: 1px; background: var(--rule); margin: 16px 0 14px; }
  .service-list {
    list-style: none; text-align: center;
    font-family: "Roboto Condensed", sans-serif; font-size: 13px;
    letter-spacing: 0.5px; line-height: 1.3; color: var(--ink-soft);
    text-transform: uppercase;
  }
</style>
</head>
<body>
<main class="canvas">

  <section class="card contact-side">
    <h1 class="contact-name">Marcus T. Hollings</h1>
    <p class="contact-role">Project Manager</p>

    <div class="icon-row">
      <span class="rule"></span>
      <span class="icon-badge" aria-label="Social profile"></span>
      <span class="icon-badge" aria-label="Social profile"></span>
      <span class="rule"></span>
    </div>
    <p class="contact-line">@hlelectricalsolutions</p>

    <div class="icon-row">
      <span class="rule"></span>
      <span class="icon-badge" aria-label="Mobile">
        <svg viewBox="0 0 12 12" fill="none" stroke="#f2f2f2" stroke-width="1.1">
          <rect x="3.5" y="1" width="5" height="10" rx="0.8"/>
          <line x1="5.3" y1="9.4" x2="6.7" y2="9.4"/>
        </svg>
      </span>
      <span class="icon-badge" aria-label="Email">
        <svg viewBox="0 0 12 12" fill="none" stroke="#f2f2f2" stroke-width="1.1">
          <rect x="1.5" y="3" width="9" height="6.5"/>
          <polyline points="1.5,3 6,7 10.5,3"/>
        </svg>
      </span>
      <span class="rule"></span>
    </div>
    <div class="contact-block">
      <p class="contact-line">(441) 555-0187</p>
      <p class="contact-line">hlelectricalsolutions@mailvento.com</p>
    </div>
  </section>

  <section class="card brand-side">
    <div class="brand-lockup">
      <span class="brand-square"></span>
      <span class="brand-name">Harbourline Electrical Solutions</span>
    </div>
    <p class="brand-sectors">Commercial Industrial Residential</p>
    <span class="brand-divider"></span>
    <ul class="service-list">
      <li>Electrical Construction &amp; Maintenance</li>
      <li>LED Lighting &amp; Automation | Data &amp; Communication</li>
      <li>Life Safety Systems (Fire Alarm / Security)</li>
    </ul>
  </section>

</main>
</body>
</html>
```